I would like to modify/update my 2 step login screen

I want a more modern looking login page for our document imaging application. I need to keep all of the same elements and buttons that currently exist. The first 2 screens are the login. The 3rd is a screenshot of the actual application home page.

```html
<!DOCTYPE html>
<html lang="en">
<head>
<meta charset="utf-8">
<title>Northfield Systems – Login Flow</title>
<link href="https://fonts.googleapis.com/css2?family=Inter:wght@400;500;600;700&display=swap" rel="stylesheet">
<style>
:root{
  --canvas:#efefef;
  --page:#fbfbfb;
  --band:#3b3b3d;
  --card:#ffffff;
  --line:#e4e4e4;
  --ink:#2a2a2a;
  --muted:#8a8a8a;
  --soft:#f1f1f1;
  --focus:#5b8bd9;
  --error:#e86262;
  --go:#4cb35a;
  --off:#d5d5d5;
  --link:#3a6fc4;
}
*{box-sizing:border-box;margin:0;padding:0}
html,body{width:1200px;height:482px;overflow:hidden;background:var(--canvas)}
body{font-family:"Inter",Arial,sans-serif;color:var(--ink)}
.board{position:absolute;left:0;top:0;width:2576px;height:1036px;transform:scale(0.46584);transform-origin:0 0}
.screen{position:absolute;width:797px;height:448px;background:var(--page);overflow:hidden}
.screen--a{left:46px;top:46px}.screen--b{left:889px;top:46px}.screen--c{left:1732px;top:46px}
.screen--d{left:46px;top:541px}.screen--e{left:889px;top:541px}.screen--f{left:1732px;top:541px}
.band{position:absolute;left:0;top:0;width:100%;height:144px;background:var(--band)}
.brand{position:absolute;top:30px;left:0;width:100%;display:flex;justify-content:center;align-items:center;gap:8px;color:#fff;font-weight:700;font-size:14px;letter-spacing:1.5px}
.brand__dot{width:22px;height:22px;border-radius:50%;background:#fff}
.card{position:absolute;left:212px;top:97px;width:373px;background:var(--card);border-radius:4px;box-shadow:0 1px 4px rgba(0,0,0,.12)}
.card__head{height:47px;padding:0 18px;display:flex;justify-content:space-between;align-items:center;border-bottom:1px solid var(--line)}
.card__title{font-size:14.5px;font-weight:600}
.card__step{text-align:right;line-height:1.5}
.card__step small{display:block;font-size:6px;color:var(--muted)}
.card__step span{font-size:7.5px}
.card__body{padding:23px 37px 24px}
.alert{color:var(--error);font-size:6.5px;text-align:center;margin:-4px 0 8px}
.field{height:31px;border:1px solid var(--line);border-radius:16px;display:flex;align-items:center;padding:0 8px 0 3px;margin-bottom:8px;background:#fff}
.field--focus{border:1.5px solid var(--focus)}
.field--error{border:1.5px solid var(--error)}
.field__icon{width:23px;height:23px;border-radius:50%;background:var(--soft);display:flex;align-items:center;justify-content:center;flex:none}
.field__text{flex:1;margin-left:11px;line-height:1.25}
.field__hint{font-size:7.5px;color:var(--muted)}
.field__label{display:block;font-size:5.5px;color:var(--muted)}
.field__value{font-size:8px}
.field__dots{font-size:9px;letter-spacing:.5px}
.field__tool{display:flex;align-items:center;gap:6px}
.field__sep{width:1px;height:12px;background:var(--line)}
.row{display:flex;align-items:center;justify-content:space-between;margin-top:12px}
.notice{display:flex;align-items:center;gap:8px;font-size:6px;line-height:1.6;margin-left:3px}
.notice__icon{width:15px;height:15px;border-radius:50%;background:var(--soft);display:flex;align-items:center;justify-content:center}
.notice b{font-weight:600}
.link{font-size:7.5px;color:var(--link)}
.btn{width:55px;height:22px;border-radius:11px;border:none;background:var(--go);color:#fff;font:600 7px "Inter",sans-serif;letter-spacing:.4px;display:flex;align-items:center;justify-content:center}
.btn--off{background:var(--off)}
.socials{display:flex;border-top:1px solid var(--line)}
.social{flex:1;height:53px;display:flex;flex-direction:column;align-items:center;justify-content:center;gap:8px;font-size:7.5px}
.social+.social{border-left:1px solid var(--line)}
.social__mark{width:11px;height:11px}
.social__mark--round{border-radius:50%;background:#4a78d0}
.social__mark--square{background:#e0803a}
.social__mark--dark{border-radius:50%;background:#1d1d1f}
.footer{position:absolute;left:0;top:395px;width:100%;text-align:center}
.footer__links{font-size:6.5px;display:flex;justify-content:center;gap:6px}
.footer__links i{color:var(--muted);font-style:normal}
.footer__copy{margin-top:8px;font-size:6px;color:var(--muted)}
</style>
</head>
<body>
<svg width="0" height="0" style="position:absolute">
  <defs>
    <symbol id="i-db" viewBox="0 0 12 12"><rect x="1.5" y="2" width="9" height="3.5" rx="1" fill="none" stroke="#555" stroke-width="1"/><rect x="1.5" y="6.5" width="9" height="3.5" rx="1" fill="none" stroke="#555" stroke-width="1"/></symbol>
    <symbol id="i-user" viewBox="0 0 12 12"><circle cx="6" cy="4" r="2.2" fill="none" stroke="#555"/><path d="M2 10.5c0-2.2 1.8-3.5 4-3.5s4 1.3 4 3.5" fill="none" stroke="#555"/></symbol>
    <symbol id="i-key" viewBox="0 0 12 12"><circle cx="7.5" cy="4.5" r="2.2" fill="none" stroke="#555"/><path d="M6 6 2 10M3.5 8.5l1 1" fill="none" stroke="#555"/></symbol>
    <symbol id="i-x" viewBox="0 0 10 10"><path d="M2 2l6 6M8 2 2 8" stroke="#888" stroke-width="1"/></symbol>
    <symbol id="i-eye" viewBox="0 0 12 12"><path d="M1 6c1.5-2.5 3-3.5 5-3.5S9.5 3.5 11 6c-1.5 2.5-3 3.5-5 3.5S2.5 8.5 1 6z" fill="none" stroke="#888" stroke-width=".9"/><circle cx="6" cy="6" r="1.5" fill="none" stroke="#888" stroke-width=".9"/><path d="M2 10 10 2" stroke="#888" stroke-width=".9"/></symbol>
    <symbol id="i-info" viewBox="0 0 10 10"><circle cx="5" cy="5" r="3.6" fill="none" stroke="#555" stroke-width=".8"/><path d="M5 4.3v2.6" stroke="#555" stroke-width=".9"/><circle cx="5" cy="3.1" r=".5" fill="#555"/></symbol>
  </defs>
</svg>

<div class="board">

  <!-- Step 1: empty -->
  <section class="screen screen--a">
    <div class="band"></div>
    <div class="brand"><span class="brand__dot"></span>NORTHFIELD SYSTEMS</div>
    <div class="card">
      <header class="card__head"><h1 class="card__title">Login</h1><div class="card__step"><small>Step 1 of 2</small><span>Please enter your Database</span></div></header>
      <div class="card__body">
        <div class="field"><span class="field__icon"><svg width="12" height="12"><use href="#i-db"/></svg></span><span class="field__text field__hint">Database</span></div>
        <div class="row"><div class="notice"><span class="notice__icon"><svg width="10" height="10"><use href="#i-info"/></svg></span><p>All activity on this site is being recorded.<br>Your IP Address is being saved as '<b>192.168.168.134</b>'.</p></div><button class="btn btn--off">NEXT</button></div>
      </div>
      <nav class="socials"><div class="social"><span class="social__mark social__mark--round"></span>Login with Orbit</div><div class="social"><span class="social__mark social__mark--square"></span>Login with Tessera</div><div class="social"><span class="social__mark social__mark--dark"></span>Login with Keyline</div></nav>
    </div>
    <footer class="footer"><div class="footer__links"><span>Privacy</span><i>•</i><span>Remote Support</span><i>•</i><span>Contact Us</span></div><p class="footer__copy">Copyright 2007-2024 Northfield Systems</p></footer>
  </section>

  <!-- Step 1: filled -->
  <section class="screen screen--b">
    <div class="band"></div>
    <div class="brand"><span class="brand__dot"></span>NORTHFIELD SYSTEMS</div>
    <div class="card">
      <header class="card__head"><h1 class="card__title">Login</h1><div class="card__step"><small>Step 1 of 2</small><span>Please enter your Database</span></div></header>
      <div class="card__body">
        <div class="field field--focus"><span class="field__icon"><svg width="12" height="12"><use href="#i-db"/></svg></span><span class="field__text"><span class="field__label">Database</span><span class="field__value">ABC12345|</span></span><svg width="10" height="10"><use href="#i-x"/></svg></div>
        <div class="row"><div class="notice"><span class="notice__icon"><svg width="10" height="10"><use href="#i-info"/></svg></span><p>All activity on this site is being recorded.<br>Your IP Address is being saved as '<b>192.168.168.134</b>'.</p></div><button class="btn">NEXT</button></div>
      </div>
      <nav class="socials"><div class="social"><span class="social__mark social__mark--round"></span>Login with Orbit</div><div class="social"><span class="social__mark social__mark--square"></span>Login with Tessera</div><div class="social"><span class="social__mark social__mark--dark"></span>Login with Keyline</div></nav>
    </div>
    <footer class="footer"><div class="footer__links"><span>Privacy</span><i>•</i><span>Remote Support</span><i>•</i><span>Contact Us</span></div><p class="footer__copy">Copyright 2007-2024 Northfield Systems</p></footer>
  </section>

  <!-- Step 1: error -->
  <section class="screen screen--c">
    <div class="band"></div>
    <div class="brand"><span class="brand__dot"></span>NORTHFIELD SYSTEMS</div>
    <div class="card">
      <header class="card__head"><h1 class="card__title">Login</h1><div class="card__step"><small>Step 1 of 2</small><span>Please enter your Database</span></div></header>
      <div class="card__body">
        <p class="alert">Invalid Database! Please enter the correct data.</p>
        <div class="field field--error"><span class="field__icon"><svg width="12" height="12"><use href="#i-db"/></svg></span><span class="field__text"><span class="field__label">Database</span><span class="field__value">ABC12345XYZ</span></span><svg width="10" height="10"><use href="#i-x"/></svg></div>
        <div class="row"><div class="notice"><span class="notice__icon"><svg width="10" height="10"><use href="#i-info"/></svg></span><p>All activity on this site is being recorded.<br>Your IP Address is being saved as '<b>192.168.168.134</b>'.</p></div><button class="btn">NEXT</button></div>
      </div>
      <nav class="socials"><div class="social"><span class="social__mark social__mark--round"></span>Login with Orbit</div><div class="social"><span class="social__mark social__mark--square"></span>Login with Tessera</div><div class="social"><span class="social__mark social__mark--dark"></span>Login with Keyline</div></nav>
    </div>
    <footer class="footer"><div class="footer__links"><span>Privacy</span><i>•</i><span>Remote Support</span><i>•</i><span>Contact Us</span></div><p class="footer__copy">Copyright 2007-2024 Northfield Systems</p></footer>
  </section>

  <!-- Step 2: empty -->
  <section class="screen screen--d">
    <div class="band"></div>
    <div class="brand"><span class="brand__dot"></span>NORTHFIELD SYSTEMS</div>
    <div class="card">
      <header class="card__head"><h1 class="card__title">Login</h1><div class="card__step"><small>Step 2 of 2</small><span>Please enter your Username and Password</span></div></header>
      <div class="card__body">
        <div class="field"><span class="field__icon"><svg width="12" height="12"><use href="#i-user"/></svg></span><span class="field__text field__hint">Username</span></div>
        <div class="field"><span class="field__icon"><svg width="12" height="12"><use href="#i-key"/></svg></span><span class="field__text field__hint">Password</span><svg width="11" height="11"><use href="#i-eye"/></svg></div>
        <div class="row"><a class="link">Forgot Password?</a><button class="btn btn--off">LOGIN</button></div>
      </div>
    </div>
    <footer class="footer"><div class="footer__links"><span>Privacy</span><i>•</i><span>Remote Support</span><i>•</i><span>Contact Us</span></div><p class="footer__copy">Copyright 2007-2024 Northfield Systems</p></footer>
  </section>

  <!-- Step 2: filled -->
  <section class="screen screen--e">
    <div class="band"></div>
    <div class="brand"><span class="brand__dot"></span>NORTHFIELD SYSTEMS</div>
    <div class="card">
      <header class="card__head"><h1 class="card__title">Login</h1><div class="card__step"><small>Step 2 of 2</small><span>Please enter your Username and Password</span></div></header>
      <div class="card__body">
        <div class="field"><span class="field__icon"><svg width="12" height="12"><use href="#i-user"/></svg></span><span class="field__text"><span class="field__label">Username</span><span class="field__value">JohnDoe123</span></span><svg width="10" height="10"><use href="#i-x"/></svg></div>
        <div class="field field--focus"><span class="field__icon"><svg width="12" height="12"><use href="#i-key"/></svg></span><span class="field__text"><span class="field__label">Password</span><span class="field__dots">●●●|</span></span><span class="field__tool"><svg width="11" height="11"><use href="#i-eye"/></svg><span class="field__sep"></span><svg width="10" height="10"><use href="#i-x"/></svg></span></div>
        <div class="row"><a class="link">Forgot Password?</a><button class="btn">LOGIN</button></div>
      </div>
    </div>
    <footer class="footer"><div class="footer__links"><span>Privacy</span><i>•</i><span>Remote Support</span><i>•</i><span>Contact Us</span></div><p class="footer__copy">Copyright 2007-2024 Northfield Systems</p></footer>
  </section>

  <!-- Step 2: error -->
  <section class="screen screen--f">
    <div class="band"></div>
    <div class="brand"><span class="brand__dot"></span>NORTHFIELD SYSTEMS</div>
    <div class="card">
      <header class="card__head"><h1 class="card__title">Login</h1><div class="card__step"><small>Step 2 of 2</small><span>Please enter your Username and Password</span></div></header>
      <div class="card__body">
        <p class="alert">Invalid Username and/or Password! Please enter the correct data.</p>
        <div class="field field--error"><span class="field__icon"><svg width="12" height="12"><use href="#i-user"/></svg></span><span class="field__text"><span class="field__label">Username</span><span class="field__value">john.doe</span></span><svg width="10" height="10"><use href="#i-x"/></svg></div>
        <div class="field field--error"><span class="field__icon"><svg width="12" height="12"><use href="#i-key"/></svg></span><span class="field__text"><span class="field__label">Password</span><span class="field__dots">●●●●●●</span></span><span class="field__tool"><svg width="11" height="11"><use href="#i-eye"/></svg><span class="field__sep"></span><svg width="10" height="10"><use href="#i-x"/></svg></span></div>
        <div class="row"><a class="link">Forgot Password?</a><button class="btn">LOGIN</button></div>
      </div>
    </div>
    <footer class="footer"><div class="footer__links"><span>Privacy</span><i>•</i><span>Remote Support</span><i>•</i><span>Contact Us</span></div><p class="footer__copy">Copyright 2007-2024 Northfield Systems</p></footer>
  </section>

</div>
</body>
</html>
```